Whitcombe Business Card Design

The name of the business is Dario Whitcombe, CPA LLC
The service that we offer is Accounting, Tax & Consulting Services. I need it to have the following items:
Dario Whitcombe, Principal
Phone Number
Email Address
Physical Address

I have attached the company logo, one in black and one in white. Please provide a design in black background and the other in white background. Please include "Accounting, Tax & Consulting Services". I want the business card to be clean and very professional.

```html
<!DOCTYPE html>
<html lang="en">
<head>
<meta charset="utf-8">
<title>Dario Whitcombe, CPA LLC — Business Cards</title>
<link href="https://fonts.googleapis.com/css2?family=Montserrat:wght@600;700&family=Roboto:wght@300;400&display=swap" rel="stylesheet">
<style>
  :root {
    --backdrop: #2b2b2b;
    --card: #ececec;
    --ink: #333335;
    --brand-red: #7d1417;
    --brand-gray: #87888b;
    --soft-white: #f1f1f1;
  }
  * { box-sizing: border-box; margin: 0; padding: 0; }
  html, body { width: 1200px; height: 1138px; overflow: hidden; background: var(--backdrop); }
  .canvas { position: relative; width: 1200px; height: 1138px; }

  .card {
    position: absolute;
    left: 273px;
    width: 620px;
    height: 376px;
    background: var(--card);
    border-radius: 16px;
    overflow: hidden;
  }
  .card--front { top: 184px; }
  .card--back { top: 606px; }

  .brand {
    position: absolute;
    left: 0; right: 0;
    text-align: center;
  }
  .brand__name {
    display: inline-flex;
    align-items: center;
    gap: 12px;
    font-family: "Montserrat", sans-serif;
    font-weight: 700;
    font-size: 27px;
    color: var(--ink);
    letter-spacing: 0.5px;
    text-transform: uppercase;
    white-space: nowrap;
  }
  .brand__square { width: 20px; height: 20px; background: var(--brand-red); display: inline-block; }
  .brand__descriptor {
    margin-top: 4px;
    font-family: "Montserrat", sans-serif;
    font-weight: 600;
    font-size: 19px;
    letter-spacing: 2.6px;
    color: var(--brand-gray);
    text-transform: uppercase;
  }
  .card--front .brand { top: 198px; }
  .card--back .brand { top: 146px; }

  .tagline {
    position: absolute;
    top: 324px; left: 0; right: 0;
    text-align: center;
    font-family: "Roboto", sans-serif;
    font-size: 16px;
    color: #2a2a2a;
  }
  .edge-strip { position: absolute; left: 0; right: 0; bottom: 0; height: 9px; display: flex; }
  .edge-strip__red { flex: 1; background: var(--brand-red); }
  .edge-strip__gray { flex: 1; background: var(--brand-gray); }

  .person-band {
    position: absolute;
    top: 205px; left: 0; right: 0;
    height: 73px;
    background: var(--brand-gray);
    display: flex; align-items: center; justify-content: center; gap: 16px;
    color: var(--soft-white);
  }
  .person-band__name {
    font-family: "Montserrat", sans-serif;
    font-weight: 700;
    font-size: 21px;
    letter-spacing: 0.8px;
    text-transform: uppercase;
  }
  .person-band__role { font-family: "Roboto", sans-serif; font-weight: 300; font-size: 17px; }

  .contact-band {
    position: absolute;
    top: 278px; left: 0; right: 0; bottom: 0;
    background: var(--brand-red);
    color: var(--soft-white);
    font-family: "Roboto", sans-serif;
    font-weight: 300;
    font-size: 16px;
    line-height: 24px;
    text-align: center;
    padding-top: 18px;
  }
</style>
</head>
<body>
<main class="canvas">
  <section class="card card--front" aria-label="Card front">
    <div class="brand">
      <div class="brand__name"><span class="brand__square"></span>Dario Whitcombe, CPA LLC</div>
      <div class="brand__descriptor">Certified Public Accountant</div>
    </div>
    <p class="tagline">Accounting, Tax &amp; Consulting Services</p>
    <div class="edge-strip"><span class="edge-strip__red"></span><span class="edge-strip__gray"></span></div>
  </section>

  <section class="card card--back" aria-label="Card back">
    <div class="brand">
      <div class="brand__name"><span class="brand__square"></span>Dario Whitcombe, CPA LLC</div>
      <div class="brand__descriptor">Certified Public Accountant</div>
    </div>
    <div class="person-band">
      <span class="person-band__name">Dario Whitcombe</span>
      <span class="person-band__role">|&nbsp; Principal</span>
    </div>
    <div class="contact-band">
      <p>P. 555-204-7318 &nbsp;|&nbsp; E: dw@whitcombecpa.com &nbsp;|&nbsp; W: whitcombecpa.com</p>
      <p>A: 482 Larkspur Avenue, Fairhaven, US 40217</p>
    </div>
  </section>
</main>
</body>
</html>
```